Veldmark Supplies Business Card

Professional business card that stand out to our potential customers. Front and back with clean modern design

Industry/Entity Type

Oil and gas

Contact Information for Business Card

Name, address, website , office phone and cell number

Requirements
Must have
• Editable files for each employee

```html
<!DOCTYPE html>
<html lang="en">
<head>
<meta charset="utf-8">
<title>Veldmark Supplies Business Card</title>
<link rel="stylesheet" href="https://fonts.googleapis.com/css2?family=Montserrat:wght@400;500;700&display=swap">
<style>
  :root {
    --backdrop: #3b3b3c;
    --card: #231f20;
    --red: #ed1c24;
    --green: #1e9e48;
    --white: #f4f4f4;
    --deboss: #322e2f;
  }
  * { margin: 0; padding: 0; box-sizing: border-box; }
  html, body {
    width: 1200px; height: 1059px; overflow: hidden;
    background: var(--backdrop);
    font-family: "Montserrat", sans-serif;
  }
  .canvas { position: relative; width: 1200px; height: 1059px; }
  .card {
    position: absolute;
    background: var(--card);
    border-radius: 24px;
    box-shadow: 0 14px 28px rgba(0,0,0,0.55);
  }
  .card--front { left: 257px; top: 100px; width: 687px; height: 391px; }
  .card--back  { left: 253px; top: 537px; width: 694px; height: 394px; }

  .brand-name {
    position: absolute;
    left: 0; width: 343px; top: 180px;
    text-align: center;
    font-weight: 700; font-size: 27px; letter-spacing: 0.5px;
    color: var(--red);
  }
  .divider {
    position: absolute; left: 343px; top: 98px;
    width: 1.5px; height: 197px; background: var(--green);
  }
  .person { position: absolute; left: 382px; top: 92px; }
  .person__name { font-weight: 700; font-size: 27px; line-height: 34px; white-space: nowrap; }
  .person__first { color: var(--red); }
  .person__last { color: var(--green); }
  .person__title { color: var(--white); font-size: 15.5px; font-weight: 400; margin-top: 2px; letter-spacing: 0.3px; }
  .accent-rule { position: absolute; left: 382px; top: 166px; width: 18px; height: 2px; background: var(--red); }

  .contact-list { position: absolute; left: 382px; top: 184px; list-style: none; }
  .contact-list li {
    display: flex; align-items: center; height: 23.2px;
    color: var(--white); font-size: 15px; letter-spacing: 0.2px; white-space: nowrap;
  }
  .contact-list svg { width: 13px; height: 13px; margin-right: 8px; flex: none; }

  .back-name {
    position: absolute; inset: 0;
    display: flex; align-items: center; justify-content: center;
    font-weight: 700; font-size: 42px; color: var(--deboss);
  }
</style>
</head>
<body>
<main class="canvas">
  <section class="card card--front" aria-label="Card front">
    <div class="brand-name">Veldmark Supplies</div>
    <div class="divider"></div>
    <div class="person">
      <p class="person__name"><span class="person__first">Daniel</span> <span class="person__last">Corvane</span></p>
      <p class="person__title">Manager</p>
    </div>
    <div class="accent-rule"></div>
    <ul class="contact-list">
      <li>
        <svg viewBox="0 0 24 24" aria-hidden="true"><path fill="#ed1c24" d="M6.6 10.8a15 15 0 0 0 6.6 6.6l2.2-2.2c.3-.3.7-.4 1-.2 1.1.4 2.3.6 3.6.6.6 0 1 .4 1 1V20c0 .6-.4 1-1 1A17 17 0 0 1 3 4c0-.6.4-1 1-1h3.5c.6 0 1 .4 1 1 0 1.3.2 2.5.6 3.6.1.3 0 .7-.2 1z"/></svg>
        1-604-555-0147
      </li>
      <li>
        <svg viewBox="0 0 24 24" aria-hidden="true"><rect x="2" y="5" width="20" height="14" rx="1.5" fill="#1e9e48"/><path d="M2.5 6l9.5 7 9.5-7" fill="none" stroke="#231f20" stroke-width="1.6"/></svg>
        dcorvane@veldmarkparts.vn
      </li>
      <li>
        <svg viewBox="0 0 24 24" aria-hidden="true"><g fill="none" stroke="#ed1c24" stroke-width="1.8"><circle cx="12" cy="12" r="9.5"/><ellipse cx="12" cy="12" rx="4" ry="9.5"/><path d="M2.5 12h19M4 7h16M4 17h16"/></g></svg>
        www.veldmarkparts.vn
      </li>
      <li>
        <svg viewBox="0 0 24 24" aria-hidden="true"><g fill="none" stroke="#1e9e48" stroke-width="1.8"><circle cx="12" cy="12" r="9.5"/><ellipse cx="12" cy="12" rx="4" ry="9.5"/><path d="M2.5 12h19M4 7h16M4 17h16"/></g></svg>
        www.veldmarkparts.com
      </li>
      <li>
        <svg viewBox="0 0 24 24" aria-hidden="true"><path fill="#ed1c24" d="M12 2a7 7 0 0 0-7 7c0 5.2 7 13 7 13s7-7.8 7-13a7 7 0 0 0-7-7zm0 9.5A2.5 2.5 0 1 1 12 6.5a2.5 2.5 0 0 1 0 5z"/></svg>
        Port Calder, Norvania
      </li>
    </ul>
  </section>

  <section class="card card--back" aria-label="Card back">
    <div class="back-name">Veldmark Supplies</div>
  </section>
</main>
</body>
</html>
```